Create modern and sleek business card for luxury real estate company

We're a "boutique" real estate office looking for a design that gets across a highly modern luxury brand. Blacks and whites are probably the best colors unless we try a silver foil for the logo. I've attached a version of our current logo here. I'd like to swap out the current font on there with Gotham Light Regular.

I'm looking to have one side of the card have the logo with the space for our agents info on the other side.

Target Market(s)

Young professionals in a "luxury" headspace

Industry/Entity Type

Real estate

Contact Information for Business Card

A place for agent name, cell number, website. The slogan "Simply Rethinking Real Estate".

Font styles to use
Other font styles liked:
• Gotham Regular

Colors

Designer to choose only greyscale colors for use in the design.

Requirements
Must have
• Matte black as the background color. Clean lines and use of contrast. A specific design aspect that will use silver foil.
Nice to have
• Up in the air on integrating a QR code
Should not have
• Any houses or other real estate related design (ex: a clip art house)

```html
<!DOCTYPE html>
<html lang="en">
<head>
<meta charset="UTF-8">
<title>Solene Realty — Business Card</title>
<link rel="stylesheet" href="https://fonts.googleapis.com/css2?family=Montserrat:wght@300;400;600&display=swap">
<style>
  :root {
    --stage: #111111;
    --card: #1e1e1e;
    --card-edge: #262626;
    --silver: #e6e6e6;
    --silver-soft: #bdbdbd;
    --divider: #7a7a7a;
    --emboss: #0d0d0d;
    --emboss-light: #2c2c2c;
  }
  * { margin: 0; padding: 0; box-sizing: border-box; }
  html, body {
    width: 1200px; height: 900px; overflow: hidden;
    background: var(--stage);
    font-family: "Montserrat", sans-serif;
  }
  .canvas {
    width: 1200px; height: 900px;
    display: flex; flex-direction: column;
    align-items: center; justify-content: center; gap: 60px;
  }
  .card {
    width: 630px; height: 360px;
    background: radial-gradient(circle at 40% 35%, var(--card-edge), var(--card) 70%);
    box-shadow: 0 20px 40px rgba(0,0,0,0.6);
    position: relative;
  }
  /* Brand lockup */
  .brand { display: flex; align-items: center; gap: 14px; }
  .brand-mark {
    width: 58px; height: 58px; border-radius: 50%;
    border: 2px solid currentColor; flex: none;
  }
  .brand-name {
    font-weight: 400; font-size: 26px; letter-spacing: 4px;
    line-height: 1.15; text-transform: uppercase;
  }
  /* Front: agent side */
  .card-front { display: flex; align-items: center; padding: 0 44px; }
  .card-front .brand { color: var(--silver); width: 260px; }
  .card-front .brand-name { font-size: 22px; }
  .divider {
    width: 1px; height: 170px; background: var(--divider);
    margin: 0 34px 0 20px;
  }
  .agent { color: var(--silver); }
  .agent-name {
    font-weight: 600; font-size: 19px; letter-spacing: 1.5px;
    text-transform: uppercase;
  }
  .agent-title { font-weight: 300; font-size: 14px; color: var(--silver-soft); margin-bottom: 14px; }
  .agent-address { font-weight: 300; font-size: 13px; line-height: 1.45; margin-bottom: 12px; }
  .contact-list { list-style: none; font-weight: 300; font-size: 13px; line-height: 1.7; }
  .contact-list li { display: flex; align-items: center; gap: 8px; }
  .contact-list svg { width: 11px; height: 11px; fill: var(--silver); flex: none; }
  /* Back: logo side */
  .card-back { display: flex; align-items: center; justify-content: center; }
  .card-back .brand {
    color: var(--emboss);
    text-shadow: 0 1px 0 var(--emboss-light);
  }
  .card-back .brand-mark {
    width: 80px; height: 80px; border-width: 3px;
    box-shadow: 0 1px 0 var(--emboss-light);
  }
  .card-back .brand-name { font-size: 36px; }
</style>
</head>
<body>
<main class="canvas">
  <section class="card card-front" aria-label="Business card front">
    <div class="brand">
      <span class="brand-mark"></span>
      <span class="brand-name">Solene<br>Realty</span>
    </div>
    <span class="divider"></span>
    <div class="agent">
      <p class="agent-name">Adrian Vale</p>
      <p class="agent-title">Founder &amp; CEO</p>
      <p class="agent-address">48 Linden Row Suite 310<br>Harbor City, Country</p>
      <ul class="contact-list">
        <li><svg viewBox="0 0 24 24"><path d="M6.6 10.8a15.1 15.1 0 0 0 6.6 6.6l2.2-2.2a1 1 0 0 1 1-.25 11.4 11.4 0 0 0 3.6.57 1 1 0 0 1 1 1V20a1 1 0 0 1-1 1A17 17 0 0 1 3 4a1 1 0 0 1 1-1h3.5a1 1 0 0 1 1 1c0 1.25.2 2.45.57 3.57a1 1 0 0 1-.25 1z"/></svg>(555) 014-2290</li>
        <li><svg viewBox="0 0 24 24"><path d="M2 5h20v14H2zm2 2v.5l8 5 8-5V7l-8 5z"/></svg>info@solenerealty.com</li>
        <li><svg viewBox="0 0 24 24"><path d="M12 2a10 10 0 1 0 0 20 10 10 0 0 0 0-20zm7.9 9h-3.4a15 15 0 0 0-1.4-6.1A8 8 0 0 1 19.9 11zM12 4c1 1.3 2.2 3.7 2.5 7h-5C9.8 7.7 11 5.3 12 4zM4.1 13h3.4a15 15 0 0 0 1.4 6.1A8 8 0 0 1 4.1 13zm3.4-2H4.1a8 8 0 0 1 4.8-6.1A15 15 0 0 0 7.5 11zm2 2h5c-.3 3.3-1.5 5.7-2.5 7-1-1.3-2.2-3.7-2.5-7zm5.6 6.1a15 15 0 0 0 1.4-6.1h3.4a8 8 0 0 1-4.8 6.1z"/></svg>www.solenerealty.com</li>
      </ul>
    </div>
  </section>

  <section class="card card-back" aria-label="Business card back">
    <div class="brand">
      <span class="brand-mark"></span>
      <span class="brand-name">Solene<br>Realty</span>
    </div>
  </section>
</main>
</body>
</html>
```